Website re-design and completion for www.brovimark.com

Graphically redesign and complete the existing site www.brovimark.com
This site intent is to:
a) introduce and educate about a new Technoloy to customers in a variety of different industries using traditional methods.
b) outline and promote the benefits and ROI of using the new techology
c) Sell our machines by showing customers the benefits and reasons to purchase from us over other suppliers
We do want to keep the overall concept. Like the home page with a slider. The most important thing to us is to increase the design of the slider. Next we need it standard layout with some attractive design to describe each product group. There are 3 product groups. Laser Cleaning Machines, Laser Welding Machines and Laser Cutting Machines

Target Market(s)

Mostly business to business.

Coding

Coded - Design and coding required

Font styles to use
Sans Serif
Other font styles liked:
• Calibri, Arial

Requirements
Must have
• A serious approach as we are targeting professionals, such as production managers, engineers and so forth
Should not have
• Annoying call to action stuff. Overly playful gimmicks.

```html
<!DOCTYPE html>
<html lang="en">
<head>
<meta charset="utf-8">
<title>Brovimark – Laser Cleaning, Welding and Cutting Machines</title>
<link href="https://fonts.googleapis.com/css2?family=Michroma&family=Montserrat:wght@400;500;600;700&display=swap" rel="stylesheet">
<style>
:root{
  --red:#a8283f;
  --blue:#137fc2;
  --grad:linear-gradient(90deg,#a8283f 0%,#137fc2 100%);
  --ink:#111;
  --muted:#6a6a6a;
  --header-bg:#f3f9fd;
  --line:#d8d8d8;
  --footer:#000;
}
*{box-sizing:border-box;margin:0;padding:0}
html,body{width:1200px;height:3337px;overflow:hidden}
body{position:relative;background:#fff;font-family:"Montserrat",Arial,sans-serif;color:var(--ink)}
.abs{position:absolute}
.display{font-family:"Michroma","Montserrat",sans-serif;text-transform:uppercase;letter-spacing:1px}
.btn{position:absolute;display:flex;align-items:center;justify-content:center;border-radius:26px;background:var(--grad);color:#fff;font-weight:700;font-size:15px}

/* header */
.site-header{position:absolute;left:0;top:0;width:1200px;height:86px;background:var(--header-bg)}
.brand{position:absolute;left:108px;top:22px;display:flex;align-items:center;gap:10px;font-weight:700;font-size:30px;color:var(--red);letter-spacing:1px}
.brand-dot{width:14px;height:14px;border-radius:50%;background:var(--blue)}
.nav{position:absolute;left:413px;top:35px;display:flex;gap:31px;font-size:12px;color:#222}
.header-cta{left:917px;top:18px;width:172px;height:46px}

/* hero */
.hero{position:absolute;left:0;top:86px;width:1200px;height:640px;background:linear-gradient(120deg,#1d2530 0%,#3a3f46 35%,#6b4a28 60%,#2b2f36 100%)}
.hero-glow{position:absolute;left:560px;top:240px;width:420px;height:260px;border-radius:50%;background:radial-gradient(closest-side,rgba(255,170,60,.75),rgba(255,140,30,0) 100%)}
.hero-dots{position:absolute;left:52px;top:280px}
.hero-dots .ring{position:absolute;left:0;top:0;width:24px;height:24px;border:2px solid var(--red);border-radius:50%}
.hero-dots .ring::after{content:"";position:absolute;left:5px;top:5px;width:10px;height:10px;border-radius:50%;background:var(--red)}
.hero-dots .dot{position:absolute;left:6px;width:12px;height:12px;border-radius:50%;background:#137fa0}
.hero-kicker{left:111px;top:232px;font-size:27px;color:#fff}
.hero-title{left:111px;top:270px;font-size:58px;color:#fff;letter-spacing:3px}
.hero-text{left:111px;top:344px;width:460px;font-size:15px;line-height:29px;color:#fff}
.hero-cta{left:111px;top:456px;width:171px;height:46px}
.hero-cut{position:absolute;left:0;top:630px}

/* about */
.about-frame{left:124px;top:819px;width:411px;height:332px;border:3px solid;border-image:linear-gradient(180deg,#a8283f,#137fc2) 1;border-right:none;border-bottom:none}
.about-frame-side{left:124px;top:819px;width:3px;height:332px;background:var(--blue)}
.about-photo{left:154px;top:845px;width:412px;height:333px;background:radial-gradient(circle at 55% 50%,#f3a24d 0%,#9a4a22 22%,#1c5a8e 50%,#0f2f55 100%)}
.about-title{left:602px;top:812px;font-size:40px}
.about-text{left:597px;top:878px;width:440px;font-size:15px;line-height:29.2px;color:var(--muted)}
.about-cta{left:602px;top:1138px;width:172px;height:46px}

/* products */
.products{position:absolute;left:0;top:1307px;width:1200px;height:580px;background:linear-gradient(115deg,#9c3650 0%,#7a4f78 40%,#1880c2 100%)}
.products-title{position:absolute;left:0;top:82px;width:1200px;text-align:center;font-size:38px;color:#fff}
.product-card{position:absolute;top:156px;width:315px;height:302px;border:2px solid #fff;border-radius:6px;overflow:hidden}
.product-label{position:absolute;left:36px;top:208px;width:241px;height:72px;border-radius:6px;background:var(--grad);color:#fff;font-size:21px;font-weight:500;text-align:center;line-height:34px;padding-top:2px}
.slider-arrow{position:absolute;top:284px}

/* benefits */
.benefits-title{left:0;top:1978px;width:1200px;text-align:center;font-size:41px;line-height:64px;letter-spacing:1.5px}
.tabs{position:absolute;left:110px;top:2211px;width:978px;height:77px;border:1px solid #bbb;border-radius:6px;display:flex;overflow:hidden;box-shadow:0 2px 4px rgba(0,0,0,.15)}
.tab{flex:1;display:flex;align-items:center;justify-content:center;font-size:21px;font-weight:500;border-left:1px solid #bbb}
.tab:first-child{border-left:none}
.tab.active{background:var(--grad);color:#fff}
.accordion{position:absolute;left:183px;top:2341px;width:829px}
.acc-item{background:#fff;border-radius:4px;box-shadow:0 2px 5px rgba(0,0,0,.18);margin-bottom:8px;height:54px;position:relative}
.acc-head{position:absolute;left:16px;top:18px;font-size:15px;font-weight:500}
.acc-icon{position:absolute;right:14px;top:19px}
.acc-item.open{height:117px}
.acc-body{position:absolute;left:19px;top:48px;width:780px;font-size:13px;line-height:26px;color:var(--muted)}

/* footer */
.footer-cut{position:absolute;left:0;top:2850px}
.footer{position:absolute;left:0;top:2935px;width:1200px;height:402px;background:var(--footer);color:#fff}
.footer h3{position:absolute;font-size:21px;font-weight:500}
.footer-links{position:absolute;left:209px;top:146px;list-style:none;font-size:14px;line-height:28.5px}
.footer-divider{position:absolute;top:75px;width:1px;height:275px;background:#888}
.footer-brand{position:absolute;left:467px;top:104px;width:260px;text-align:center}
.footer-brand .name{display:inline-flex;align-items:center;gap:8px;font-size:30px;font-weight:700;color:var(--red);letter-spacing:1px}
.footer-brand .name i{width:12px;height:12px;border-radius:50%;background:var(--blue);display:inline-block}
.footer-copy{position:absolute;left:467px;top:190px;width:260px;text-align:center;font-size:14px;line-height:28px}
.contact{position:absolute;left:840px;top:146px;font-size:14px;line-height:29px}
.contact .label{display:flex;align-items:center;gap:8px;font-weight:600}
.contact .value{padding-left:21px}
</style>
</head>
<body>

<header class="site-header">
  <div class="brand"><span class="brand-dot"></span>BROVIMARK</div>
  <nav class="nav"><span>HOME</span><span>ABOUT US</span><span>OUR SERVICES</span><span>PRODUCTS</span><span>CONTACT US</span></nav>
  <div class="btn header-cta">Get In Touch</div>
</header>

<section class="hero" role="img" aria-label="Laser cutting head throwing sparks over a metal sheet">
  <div class="hero-glow"></div>
</section>
<div class="hero-dots abs" style="left:52px;top:280px">
  <span class="ring"></span>
  <span class="dot" style="top:35px"></span>
  <span class="dot" style="top:61px"></span>
  <span class="dot" style="top:87px"></span>
</div>
<div class="abs display hero-kicker">Welcome to</div>
<h1 class="abs display hero-title">Brovimark</h1>
<p class="abs hero-text">Lorem Ipsum is simply dummy text of the printing and typesetting industry. Lorem Ipsum has been the industry's standard dummy text ever since the 1500s,</p>
<div class="btn hero-cta">Get Started</div>
<svg class="hero-cut" width="1200" height="100" viewBox="0 0 1200 100">
  <defs><linearGradient id="cutGrad" x1="0" x2="1"><stop offset="0" stop-color="#1e6aa8"/><stop offset="1" stop-color="#a8283f"/></linearGradient></defs>
  <polygon points="0,14 181,96 1200,14 1200,100 0,100" fill="#fff"/>
  <polygon points="0,14 181,82 1200,14 181,96" fill="url(#cutGrad)"/>
</svg>

<section>
  <div class="abs about-frame"></div>
  <div class="abs about-frame-side"></div>
  <div class="abs about-photo" role="img" aria-label="Laser nozzle glowing over a machined metal part"></div>
  <h2 class="abs display about-title">About us</h2>
  <p class="abs about-text">With unmatched precision, laser welding is easy to learn, energy efficient, and remarkably fast compared to MIG and TIG welding. Handheld laser welding machines offer unparalleled speed, precision, and ease compared to traditional methods like MIG and TIG welding.For environmentally friendly, non-contact cleaning and surface prep, laser cleaning systems help you achieve amazing results in rust removal and material preparation.</p>
  <div class="btn about-cta">Read More</div>
</section>

<section class="products">
  <h2 class="display products-title">Our products</h2>
  <svg class="slider-arrow" style="left:28px" width="50" height="50" viewBox="0 0 50 50"><circle cx="25" cy="25" r="23" fill="none" stroke="#fff" stroke-width="3"/><path d="M29 14 L18 25 L29 36" fill="none" stroke="#fff" stroke-width="3" stroke-linecap="round"/></svg>
  <div class="product-card" style="left:110px;background:linear-gradient(135deg,#8d8f8f,#c9c6c0 50%,#6d6e6e)" role="img" aria-label="Metal gear part being laser cleaned">
    <div class="product-label">Laser Cleaning<br>Machines</div>
  </div>
  <div class="product-card" style="left:439px;background:linear-gradient(180deg,#f4f4f4,#e8e8e8)" role="img" aria-label="Black portable laser welding unit on wheels">
    <div class="product-label">Laser Welding<br>Machines</div>
  </div>
  <div class="product-card" style="left:772px;background:linear-gradient(160deg,#0d4b8a,#2b7fc4 55%,#0b2e5c)" role="img" aria-label="Laser cutting heads over a sheet with sparks">
    <div class="product-label">Laser Cutting<br>Machines</div>
  </div>
  <svg class="slider-arrow" style="left:1117px" width="50" height="50" viewBox="0 0 50 50"><circle cx="25" cy="25" r="23" fill="none" stroke="#fff" stroke-width="3"/><path d="M21 14 L32 25 L21 36" fill="none" stroke="#fff" stroke-width="3" stroke-linecap="round"/></svg>
</section>

<section>
  <h2 class="abs display benefits-title">The benefits and reasons to<br>purchase from us over other<br>suppliers</h2>
  <div class="tabs">
    <div class="tab active">Laser Cleaning Equipment</div>
    <div class="tab">Laser Welding Machines</div>
    <div class="tab">Laser Cutting Machines</div>
  </div>
  <div class="accordion">
    <div class="acc-item"><span class="acc-head">No Consumables Required</span><svg class="acc-icon" width="16" height="16"><path d="M8 1v14M1 8h14" stroke="#111" stroke-width="3"/></svg></div>
    <div class="acc-item"><span class="acc-head">Environmentally Friendly</span><svg class="acc-icon" width="16" height="16"><path d="M8 1v14M1 8h14" stroke="#111" stroke-width="3"/></svg></div>
    <div class="acc-item"><span class="acc-head">No Mechanical Contact</span><svg class="acc-icon" width="16" height="16"><path d="M8 1v14M1 8h14" stroke="#111" stroke-width="3"/></svg></div>
    <div class="acc-item"><span class="acc-head">Minimal Thermal Impact</span><svg class="acc-icon" width="16" height="16"><path d="M8 1v14M1 8h14" stroke="#111" stroke-width="3"/></svg></div>
    <div class="acc-item"><span class="acc-head">Increased Productivity</span><svg class="acc-icon" width="16" height="16"><path d="M8 1v14M1 8h14" stroke="#111" stroke-width="3"/></svg></div>
    <div class="acc-item open"><span class="acc-head">Precision</span><svg class="acc-icon" width="22" height="16"><path d="M1 8h20" stroke="#111" stroke-width="3"/></svg>
      <p class="acc-body">Laser cleaning is often used by art restoration experts. The laser settings can be adjusted to gently remove only certain layers of paint or contaminents from paintings, sculptures and other art work.</p>
    </div>
  </div>
</section>

<svg class="footer-cut" width="1200" height="90" viewBox="0 0 1200 90">
  <defs><linearGradient id="footGrad" x1="0" x2="1"><stop offset="0" stop-color="#137fc2"/><stop offset="1" stop-color="#a8283f"/></linearGradient></defs>
  <polygon points="0,90 1020,5 1200,90" fill="url(#footGrad)"/>
  <polygon points="0,90 1020,17 1200,90" fill="#000"/>
</svg>
<footer class="footer">
  <h3 style="left:205px;top:83px">Quick Links</h3>
  <ul class="footer-links"><li>Home</li><li>About Us</li><li>Our Services</li><li>Products</li><li>Contact Us</li></ul>
  <div class="footer-divider" style="left:436px"></div>
  <div class="footer-brand"><span class="name"><i></i>BROVIMARK</span></div>
  <p class="footer-copy">2024 Copyright © Brovimark |<br>All Rights Reserved</p>
  <div class="footer-divider" style="left:762px"></div>
  <h3 style="left:843px;top:83px">Contact Details</h3>
  <div class="contact">
    <div class="label"><svg width="13" height="14" viewBox="0 0 13 14"><path d="M3 1 L5 4 L4 6 Q5 9 8 10 L10 9 L12 11 L10 13 Q2 12 1 3 Z" fill="#fff"/></svg>Call Us</div>
    <div class="value">555-014-2287</div>
    <div class="label"><svg width="14" height="10" viewBox="0 0 14 10"><rect x="0.5" y="0.5" width="13" height="9" fill="none" stroke="#fff"/><path d="M1 1 L7 6 L13 1" fill="none" stroke="#fff"/></svg>Email:</div>
    <div class="value">info@brovimark.com</div>
    <div class="label"><svg width="12" height="15" viewBox="0 0 12 15"><path d="M6 14 Q0 7 1 5 A5 5 0 0 1 11 5 Q12 7 6 14 Z" fill="#fff"/><circle cx="6" cy="5" r="2" fill="#000"/></svg>Location</div>
    <div class="value">Lakemont, IL 60100 Brovimark<br>Product categories</div>
  </div>
</footer>

</body>
</html>
```